Need website redesign!

I have a site, www.mapleridgefitcamp.example

I am looking to have it redesigned to make it simpler, and encourage people who hit the home page to click on a service, opt in, or contact me for more info. Having a video front and center with icons representing the services we offer around it may be a good idea, but I am open to YOUR design. Conversion is my goal. I want it to be friendly, but convey the fun and ENERGY of my bootcamp. Scrolling pics on home page so people can get a feel for our bootcamp is recommended as well.

```html
<!DOCTYPE html>
<html lang="en">
<head>
<meta charset="utf-8">
<title>Maple Ridge Fit Camp</title>
<link href="https://fonts.googleapis.com/css2?family=Raleway:wght@400;500;600;700;800&display=swap" rel="stylesheet">
<style>
:root{
  --red:#ec1c2b;
  --navy:#15152e;
  --black:#000;
  --footer:#1f1f1f;
  --grey:#efedea;
  --text:#2a2a3a;
  --blue:#3b5998;
  --white:#fff;
  --map:#e4e2dc;
}
*{margin:0;padding:0;box-sizing:border-box}
html,body{width:671px;height:1200px;overflow:hidden;background:var(--white)}
body{position:relative;font-family:'Raleway',sans-serif;color:var(--text)}
.abs{position:absolute}
.site-header{left:0;top:0;width:671px;height:57px;background:var(--black);border-bottom:2px solid var(--red)}
.brand{color:var(--white);font-weight:700;font-size:11px;line-height:13px;white-space:nowrap}
.brand-header{left:51px;top:22px}
.nav a{font-size:7px;font-weight:700;color:var(--red);text-decoration:none;text-transform:uppercase;position:absolute;top:25px;white-space:nowrap}
.nav a.active{color:var(--white)}
.hero{left:0;top:57px;width:671px;height:271px;background:linear-gradient(100deg,#d9c79a 0%,#b89a6a 25%,#2fa9a9 45%,#c4a67c 65%,#d8cbb6 85%,#efe6da 100%)}
.hero-title{left:50px;top:80px;color:var(--red);font-weight:700;font-size:22px;line-height:27px}
.hero-form{left:437px;top:91px;width:143px;height:183px;background:rgba(225,215,205,.85)}
.hero-form-head{height:54px;background:var(--navy);border-bottom:2px solid var(--red);color:var(--white);font-size:8.4px;font-weight:700;line-height:11px;padding:10px 13px 0 13px}
.label{font-size:6.5px;font-weight:600;color:var(--navy);line-height:7px}
.input{border:1px solid var(--red);background:var(--white);font-size:6px;color:#999;padding:0 6px;display:flex;align-items:center}
.btn{font-size:6.3px;font-weight:800;text-transform:uppercase;color:var(--white);display:flex;align-items:center;justify-content:center;white-space:nowrap}
.btn-dark{background:var(--navy)}
.btn-red{background:var(--red);font-weight:500;text-transform:none}
.btn-blue{background:var(--blue)}
.band{left:0;top:328px;width:671px;height:58px;background:var(--navy);color:var(--white);font-size:15px;font-weight:500;display:flex;align-items:center;justify-content:center}
.video{left:51px;top:408px;width:189px;height:147px;background:var(--black)}
.video-title{left:6px;top:6px;color:var(--white);font-size:6.5px;font-weight:500}
.video-frame{left:53px;top:18px;width:83px;height:108px;background:linear-gradient(#d7c9a8,#a8957a)}
.video-bar{left:0;top:129px;width:189px;height:3px;background:#555}
.video-bar::before{content:"";position:absolute;left:0;top:0;width:13px;height:3px;background:var(--red)}
.video-time{left:57px;top:136px;color:var(--white);font-size:5.5px}
.about-title{left:268px;top:428px;font-size:16px;font-weight:500;color:var(--navy)}
.about-body{left:268px;top:453px;width:245px;font-size:6.2px;line-height:12px;color:var(--text)}
.section-rule{left:51px;top:589px;width:575px;height:1px;background:#ccc}
.section-title{left:275px;top:578px;width:122px;height:22px;background:var(--white);font-size:15px;font-weight:500;text-align:center;line-height:22px;color:var(--navy)}
.arrow{top:579px;width:20px;height:20px;border-radius:50%;background:#ececec}
.card{top:632px;width:139px;height:110px;background:var(--grey)}
.card-img{left:0;top:0;width:139px;height:73px}
.card-title{left:0;top:77px;width:139px;text-align:center;font-size:13px;color:var(--navy)}
.card-btn{left:45px;top:105px;width:50px;height:13px}
.optin{left:51px;top:776px;width:575px;height:97px;background:var(--grey);border-bottom:2px solid var(--red)}
.optin-title{left:28px;top:19px;color:var(--red);font-size:14.5px;font-weight:700;line-height:18px}
.tagline{left:0;top:896px;width:671px;text-align:center;font-size:12.5px;line-height:15.5px;color:var(--navy)}
.tagline strong{color:var(--red);font-weight:800}
.thumb{top:975px;width:80px;height:60px}
.gallery-cta{left:476px;top:975px;width:150px;height:60px;background:var(--red);color:var(--white);font-size:12.5px;font-weight:700;line-height:15.5px;padding:9px 14px}
.footer{left:0;top:1076px;width:671px;height:100px;background:var(--footer)}
.brand-footer{left:53px;top:1092px}
.address{left:53px;top:1132px;color:var(--white);font-size:6.3px;line-height:7.8px;font-style:normal}
.footer-links{left:354px;top:1094px;list-style:none}
.footer-links li{color:var(--white);font-size:6.3px;line-height:12px}
.footer-dash{left:336px;top:1098px;width:9px;height:2px;background:var(--red)}
.loc-label{left:449px;top:1090px;color:var(--white);font-size:6.3px}
.map{left:449px;top:1101px;width:177px;height:69px;background:var(--map)}
.bottom-bar{left:0;top:1176px;width:671px;height:24px;background:var(--black);color:var(--white);font-size:6.3px}
.social{top:1181px;width:12px;height:12px;border-radius:50%}
</style>
</head>
<body>

<header class="abs site-header"></header>
<div class="abs brand brand-header">Maple Ridge Fit Camp</div>
<nav class="abs nav" style="left:0;top:0;width:671px;height:57px">
  <a class="active" style="left:369px">Home</a>
  <a style="left:404px">Services</a>
  <a style="left:452px">Classes</a>
  <a style="left:497px">About Us</a>
  <a style="left:547px">FAQ's</a>
  <a style="left:581px">Contact Us</a>
</nav>

<section class="abs hero" role="img" aria-label="Photo of a smiling woman in workout clothes doing a side-lying leg exercise on a mat"></section>
<h1 class="abs hero-title">Morning,<br>Evening and<br>Weekend Hours!</h1>
<form class="abs hero-form">
  <div class="hero-form-head">Leave your email for a<br>FREE week of bootcamp,<br>NO OBLIGATION</div>
  <div class="abs label" style="left:13px;top:63px">Name</div>
  <div class="abs input" style="left:13px;top:73px;width:114px;height:18px">Enter Your Name</div>
  <div class="abs label" style="left:13px;top:102px">Email</div>
  <div class="abs input" style="left:13px;top:111px;width:114px;height:18px">Enter Your Email ID</div>
  <div class="abs btn btn-dark" style="left:13px;top:144px;width:81px;height:18px">Get Started Now</div>
</form>

<div class="abs band">Fat Loss Bootcamps, Martial Arts, Yoga, Kids Fitness, Personal Training</div>

<div class="abs video">
  <div class="abs video-title">Dan R lost 15 pounds in just 17 sessi...</div>
  <div class="abs video-frame" role="img" aria-label="Video still of a client talking to the camera"></div>
  <div class="abs video-bar"></div>
  <svg class="abs" style="left:12px;top:135px" width="10" height="10" viewBox="0 0 10 10"><path d="M2 1 L9 5 L2 9Z" fill="#ccc"/></svg>
  <div class="abs video-time">0:00 / 0:16</div>
</div>
<h2 class="abs about-title">What is Maple Ridge Fit Camp</h2>
<p class="abs about-body">Lorem Ipsum is simply dummy text of the printing and typesetting industry. Lorem Ipsum has been the industry's standard dummy text ever since the 1500s, when ... unknown printer took a galley of type and scrambled it to make a type specimen book.Lorem Ipsum is simply standard dummy text ever since the 1500s, when ... unknown printer took a galley of type and scrambled it to make a type specimen book.</p>
<div class="abs btn btn-red" style="left:268px;top:534px;width:46px;height:14px">Read More</div>
<div class="abs btn btn-dark" style="left:322px;top:534px;width:86px;height:14px">Get Started Now</div>
<div class="abs btn btn-blue" style="left:412px;top:534px;width:109px;height:14px">Follow Us On Social</div>

<div class="abs section-rule"></div>
<div class="abs section-title">Our Services</div>
<div class="abs arrow" style="left:257px"><svg width="20" height="20"><path d="M12 5 L7 10 L12 15" stroke="#aaa" stroke-width="1.4" fill="none"/></svg></div>
<div class="abs arrow" style="left:399px"><svg width="20" height="20"><path d="M8 5 L13 10 L8 15" stroke="#222" stroke-width="1.4" fill="none"/></svg></div>

<article class="abs card" style="left:51px"><div class="abs card-img" role="img" aria-label="Group training with battle ropes" style="background:linear-gradient(#8a8a8a,#2a2a2a)"></div><div class="abs card-title">Boot Camp</div><div class="abs btn btn-red card-btn">Read More</div></article>
<article class="abs card" style="left:196px"><div class="abs card-img" role="img" aria-label="Personal training with suspension straps" style="background:linear-gradient(#b9b9b9,#4a4a4a)"></div><div class="abs card-title">Personal Training</div><div class="abs btn btn-red card-btn">Read More</div></article>
<article class="abs card" style="left:342px"><div class="abs card-img" role="img" aria-label="Yoga instructor in sportswear" style="background:linear-gradient(#3a2a22,#111)"></div><div class="abs card-title">Yoga</div><div class="abs btn btn-red card-btn">Read More</div></article>
<article class="abs card" style="left:487px"><div class="abs card-img" role="img" aria-label="Kid doing agility training in gym" style="background:linear-gradient(#c55a66,#3a3a3a)"></div><div class="abs card-title">Kids Sports/ Agility</div><div class="abs btn btn-red card-btn">Read More</div></article>

<section class="abs optin">
  <h3 class="abs optin-title">Leave your email for a<br>FREE week of bootcamp,<br>NO OBLIGATION</h3>
  <div class="abs label" style="left:231px;top:30px">Name</div>
  <div class="abs input" style="left:231px;top:40px;width:113px;height:18px">Enter Your Name</div>
  <div class="abs label" style="left:352px;top:30px">Email</div>
  <div class="abs input" style="left:352px;top:40px;width:113px;height:18px">Enter Your Email ID</div>
  <div class="abs btn btn-dark" style="left:471px;top:40px;width:81px;height:18px">Get Started Now</div>
</section>

<p class="abs tagline">A fun, friendly, and effective place for you to shed serious fat,<br>build tight lean muscle, and have the time of your life doing it.<br>So...what are you waiting for? Register now and try us out <strong>RISK FREE!</strong></p>

<div class="abs thumb" style="left:50px;background:linear-gradient(#6d7a6a,#3d4a3d)" role="img" aria-label="Woman doing crunches"></div>
<div class="abs thumb" style="left:135px;background:linear-gradient(#8aa25a,#4d6a32)" role="img" aria-label="Group photo outdoors"></div>
<div class="abs thumb" style="left:220px;background:linear-gradient(#a9a9a9,#3d3d3d)" role="img" aria-label="Suspension strap workout"></div>
<div class="abs thumb" style="left:305px;background:linear-gradient(#9fb66a,#5c7a36)" role="img" aria-label="Outdoor exercise on grass"></div>
<div class="abs thumb" style="left:390px;background:linear-gradient(#6fb8a8,#3f8072)" role="img" aria-label="Indoor lunges class"></div>
<div class="abs gallery-cta">See Our<br>Complete<br>Photo Gallery
  <svg class="abs" style="left:122px;top:14px" width="20" height="32"><path d="M2 1 L18 16 L2 31" stroke="#fff" stroke-width="1.2" fill="none"/></svg>
</div>

<footer class="abs footer"></footer>
<div class="abs brand brand-footer">Maple Ridge Fit Camp</div>
<address class="abs address">Hillcrest Martial Arts-Cedar Glen<br>1180 Birchwood Lane, Maple Ridge, MD 21900<br><span style="display:block;height:4px"></span>Oakdale Maple Ridge Fit<br>4410 Commerce Road,Suite B, Oakdale, MD 21910</address>
<div class="abs footer-dash"></div>
<ul class="abs footer-links"><li>Home</li><li>Services</li><li>Classes</li><li>About Us</li><li>Join Now</li><li>Contact Us</li></ul>
<div class="abs loc-label">Our Locations &#8744;</div>
<div class="abs map" role="img" aria-label="Street map showing the gym location"></div>

<div class="abs bottom-bar">
  <span class="abs" style="left:53px;top:8px">© 2014 Maple Ridge Fit Camp</span>
  <span class="abs" style="left:449px;top:8px">Privacy Policy &nbsp;|&nbsp;</span>
  <span class="abs" style="left:503px;top:8px">Disclaimer</span>
</div>
<div class="abs social" style="left:582px;background:#3b5998"></div>
<div class="abs social" style="left:598px;background:#1da1f2"></div>
<div class="abs social" style="left:614px;background:#dd4b39"></div>

</body>
</html>
```